Catering Menu Package

I currently have a complete menu package, which we have redesigned as far as content, now I need to it put together in a catalog type format. It is essentially 10-12 pages in length, and will be sent for print production. Upon receiving a final edit
Updates

I have added an example gif to the project.

I did this free hand this basically what I am looking for. please change text and type to whatever you think would look best. This is a total rough design so, feel free to change any and everything. The text for the page is on the word documents. If you need more images let me know I am in the process of getting as many images uploaded for your use.

Project Deadline Extended
Reason: I figured we got a late jump with questions, so i am extending a few days .

Target Market(s)

The target market is business who wish to have catered luncheons, breakfasts , meetings

Industry/Entity Type

Catering

Requirements
Must have
• I have attached a copy of the text that what we want in the package, our logo, and i have also attached a catering package of another company to give you an idea what the finished product will be
Should not have
• It should not look identical to the example catering packages, these are for some inspiration we want our own design with the same type of look and feel

```html
<!DOCTYPE html>
<html lang="en">
<head>
<meta charset="utf-8">
<title>Light Breakfast Menu – Harford Valley Caterers</title>
<link rel="stylesheet" href="https://fonts.googleapis.com/css2?family=Italianno&family=Lora:ital,wght@0,400;1,600&family=Barlow:wght@400&display=swap">
<style>
  :root {
    --page-edge: #e6dcd8;
    --page-white: #ffffff;
    --heading-pink: #b04d95;
    --heading-plum: #7a3f8f;
    --body-ink: #5b4b45;
    --title-ink: #3d3432;
    --note-ink: #2e2a28;
    --brand-ink: #2b2624;
    --brand-mark: #d9692a;
  }
  * { margin: 0; padding: 0; box-sizing: border-box; }
  html, body { width: 1200px; height: 927px; overflow: hidden; }
  body {
    position: relative;
    background: linear-gradient(100deg, var(--page-edge) 0%, #f1ebe9 16%, var(--page-white) 55%);
    font-family: "Lora", Georgia, serif;
    color: var(--body-ink);
  }
  .brand {
    position: absolute; left: 27px; top: 30px; width: 134px;
    display: flex; flex-direction: column; align-items: center; gap: 14px;
  }
  .brand-mark {
    width: 96px; height: 96px; border-radius: 50%;
    background: var(--brand-mark);
  }
  .brand-name {
    font-family: "Lora", Georgia, serif; font-weight: 400;
    font-size: 22px; line-height: 1.1; text-align: center;
    color: var(--brand-ink);
  }
  .page-title {
    position: absolute; left: 197px; top: 44px;
    font-family: "Italianno", cursive; font-weight: 400;
    font-size: 60px; color: var(--title-ink);
  }
  .menu-column { position: absolute; width: 450px; }
  .menu-column.left { left: 197px; top: 152px; }
  .menu-column.right { left: 689px; top: 218px; }
  .menu-item { margin-bottom: 27px; }
  .menu-item h2 {
    font-style: italic; font-weight: 600; font-size: 19px;
    color: var(--heading-pink); line-height: 1.2;
  }
  .menu-column.right h2 { color: var(--heading-plum); }
  .menu-item p { font-size: 16.3px; line-height: 24.5px; }
  .add-on {
    font-style: italic; font-size: 16px; margin: -2px 0 28px;
    word-spacing: 2px;
  }
  .add-on .price { margin-left: 26px; }
  .footnote {
    position: absolute; left: 197px; top: 628px;
    font-family: "Barlow", Arial, sans-serif; font-size: 15px;
    line-height: 19px; color: var(--note-ink);
  }
  .photo { position: absolute; top: 710px; height: 217px; }
  .photo.hot-plate { left: 183px; width: 323px; background: linear-gradient(135deg, #e8a043, #f3d36a 55%, #8a4a2a); }
  .photo.bagel { left: 517px; width: 233px; background: linear-gradient(160deg, #cfb79a, #a88b6b 60%, #e6e1da); }
  .photo.fruit-bowl { left: 755px; width: 227px; background: radial-gradient(circle at 50% 45%, #d9c24a, #c2443a 45%, #ffffff 72%); }
  .photo.fruit-table { left: 989px; width: 211px; background: linear-gradient(150deg, #c9a36a, #b3402f 55%, #e9d9b8); }
</style>
</head>
<body>
  <header class="brand">
    <span class="brand-mark"></span>
    <span class="brand-name">Harford Valley Caterers</span>
  </header>

  <h1 class="page-title">Light Breakfast</h1>

  <section class="menu-column left">
    <article class="menu-item">
      <h2>Quick and Easy</h2>
      <p>French Pastry, a Fresh Baked Gourmet Muffin, &amp;<br>Whole Fresh Fruit (featuring Local Apples &amp; Peaches,<br>California Oranges, or Bananas).</p>
    </article>
    <article class="menu-item">
      <h2>Fast Farmhouse</h2>
      <p>Fresh baked Breakfast Bread &amp; Buttery Biscuits,<br>Whipped Butter &amp; House-made Strawberry Jam<br>(featuring Local Apples &amp; Peaches, California<br>Oranges, or Bananas).</p>
    </article>
    <article class="menu-item">
      <h2>Light and Lean</h2>
      <p>Individual Yogurt, Fresh Fruit &amp; Berry Cups &amp;<br>House-made Granola.</p>
    </article>
  </section>

  <section class="menu-column right">
    <article class="menu-item">
      <h2>New Yorker</h2>
      <p>Brooklyn Bagel, Whipped Cream Cheese, House-made<br>Strawberry Jam &amp; Local Fruit Jellies, Whipped Butter,<br>&amp; Whole Fresh Fruit (featuring Local Apples &amp;<br>Peaches, California Oranges, or Bananas).</p>
    </article>
    <p class="add-on">Add Smoked Salmon <span class="price">$&amp;.&amp;&amp;</span></p>
    <article class="menu-item">
      <h2>City Farmhouse</h2>
      <p>Fresh Baked Buttery Biscuits, Gourmet Muffins &amp;<br>Breakfast Breads, Brooklyn Bagels, Whole Fresh Fruit<br>(featuring Local Apples &amp; Peaches, California<br>Oranges, or Bananas), Whipped Butter &amp; Cream<br>Cheese, House-made Strawberry Jam &amp; Local Fruit<br>Jellies.</p>
    </article>
  </section>

  <p class="footnote">All Prices are per Person, with a 10 person minimum order per item chosen.<br>Local Products used when available &amp; in season</p>

  <div class="photo hot-plate" role="img" aria-label="Photo of scrambled eggs, bacon and sausage links on a plate"></div>
  <div class="photo bagel" role="img" aria-label="Photo of a toasted seeded bagel with butter pats"></div>
  <div class="photo fruit-bowl" role="img" aria-label="Photo of a bowl of mixed fresh fruit with mint"></div>
  <div class="photo fruit-table" role="img" aria-label="Photo of apples, jam, bread and a teapot on a breakfast table"></div>
</body>
</html>
```